Stage Design Company Business Card

We are looking to step up up our business card design for our team.

We are a Full service Design and Consultation company for Stage and TV with an emphasis in Theatrical Lighting.

We like our materials to be clean and modern with solid colors free of patterns and gradients. Our brand consists of 4 primary colors Purple, Black, Grey, and White. Provided is our Word Mark as well as our Symbol Logo.

We would like our cards to leave an impression beyond the information, show our attention to design and detail, and make our marks an easily recognized feature (together or apart) for our clients.

We need a warm approachable comfortable feel for some clients, and a professional flair for the board member type clients.

Attached are our brand elements, and our existing cards to give a sense of our style and a glipse at the information we provide on our cards.

Target Market(s)

broad client base from church leaders to high school teachers and architects.

Industry/Entity Type

Business

Contact Information for Business Card

We format our phone number with periods not parenthesis or dashes. Information will be edited for each of our team members, and team member specific cards are not part of this scope, but rather a template so to speak.

Font styles to use
Sans Serif

Colors
6b449b
ffffff
000000
333333
aaaaaa

Requirements
Must have
• Wordmark and logo mark present (does not need to exist on the same side of card)
• Brand Colors,
• Name, Phone, Email, Address.
• Unique choices that make someone stop and take a second look
Nice to have
• It would be nice to somehow convey what we DO, as our brand name does not lend itself to this, outside of an obvious tagline though.....
• social media if not crowded. all of our handles match (instagram, twitter, facebook)
Should not have
• "clipart"

```html
<!DOCTYPE html>
<html lang="en">
<head>
<meta charset="utf-8">
<title>Vesper Business Card</title>
<link href="https://fonts.googleapis.com/css2?family=Source+Sans+3:ital,wght@0,400;0,600;0,700;1,600;1,700&display=swap" rel="stylesheet">
<style>
  :root {
    --stage: #1b1b1b;
    --card-light: #f2f2f2;
    --card-purple: #3a2466;
    --ink-purple: #2e1a5e;
    --ink-grey: #3a3a3a;
    --mark-grey: #c9c9ce;
    --tagline: #d9d9e2;
  }
  * { box-sizing: border-box; margin: 0; padding: 0; }
  html, body {
    width: 1200px; height: 900px; overflow: hidden;
    background: var(--stage);
    font-family: "Source Sans 3", "Myriad Pro", Arial, sans-serif;
  }
  .canvas { position: relative; width: 1200px; height: 900px; }
  .card {
    position: absolute; top: 170px; width: 347px; height: 561px;
    text-align: center;
  }
  .card--front { left: 259px; background: var(--card-light); }
  .card--back { left: 631px; background: var(--card-purple); }

  .brand-name {
    position: absolute; left: 0; right: 0;
    font-weight: 600; letter-spacing: 0.3em; padding-left: 0.3em;
  }
  .card--front .brand-name { top: 145px; font-size: 40px; color: var(--ink-purple); }

  .person { position: absolute; left: 0; right: 0; top: 336px; }
  .person__name { font-size: 23px; font-weight: 600; color: var(--ink-purple); line-height: 1.2; }
  .person__role { font-size: 15px; color: var(--ink-grey); margin-top: 3px; }

  .contact { position: absolute; left: 0; right: 0; top: 403px; font-size: 15px; line-height: 21px; color: var(--ink-purple); }
  .contact__label { font-weight: 700; }
  .contact__email { color: var(--ink-grey); }
  .contact__email .contact__label { color: var(--ink-purple); }
  .contact__web { font-weight: 700; }

  .address { position: absolute; left: 0; right: 0; top: 480px; font-size: 15px; line-height: 17px; color: var(--ink-grey); }

  .brand-dot {
    position: absolute; left: 128px; top: 140px; width: 90px; height: 90px;
    border-radius: 50%; background: var(--mark-grey);
  }
  .card--back .brand-name { top: 322px; font-size: 40px; color: var(--mark-grey); }

  .tagline {
    position: absolute; left: 0; right: 0; top: 458px;
    font-size: 16.5px; font-weight: 700; font-style: italic;
    line-height: 21.5px; color: var(--tagline);
  }
</style>
</head>
<body>
<main class="canvas">
  <section class="card card--front">
    <div class="brand-name">VESPER</div>
    <div class="person">
      <div class="person__name">JOHN SMITH</div>
      <div class="person__role">Managing Director</div>
    </div>
    <div class="contact">
      <div><span class="contact__label">P:</span> 823-456-7890</div>
      <div class="contact__email"><span class="contact__label">E:</span> info@youremail.com</div>
      <div class="contact__web">www.websitename.com</div>
    </div>
    <div class="address">
      <div>1234, Address Goes Here</div>
      <div>Country Name, 123456</div>
    </div>
  </section>

  <section class="card card--back">
    <div class="brand-dot"></div>
    <div class="brand-name">VESPER</div>
    <p class="tagline">Design and Consultation company<br>for Stage and TV with an<br>emphasis in Theatrical Lighting.</p>
  </section>
</main>
</body>
</html>
```